Norvane Website Design (New Start Up Investment Management Firm)

We need a website designed. We have attached a Powerpoint with our proposed website content (which is quite minimal), the format is just a suggestion but we would like to see your alternative and improved ideas. We are a boutique investment firm so are looking for something sleek and professional. I have included on the last page of the attachment our brand colours and font styles as well as attaching our logo design. We would like the successful designer to design the website and build the buttons etc.

On the "Contact Us" page, we are open to suggestions on how best to show the map, whether is should be static or open a google maps page. We would like the phone number and email address to be set up so people can click on them on their phone and it calls us or emails us directly.

We would prefer not to have photos of landscapes on the site.
Our website is hosted on a Linux based website.

We would also like 3 links at the bottom of each page for links to pdfs:
- Disclaimer, Terms and Conditions of Web Site Use
- Stewardship
- Pillar III

Target Market(s)

Institutional Investors

Industry/Entity Type

Investment

Coding

Coded - Design and coding required

Number of Pages Required

3 page

Font styles to use
Other font styles liked:
• Logo: Lato, Text: Source Sans Pro

Colors

Designer to choose colors to be used in the design.

Requirements
Must have
• The website must use the colours and fonts on the last page of the attached powerpoint. I can't see an option to select the exact colour palette below so please look at the PPT.
• For others please see Project description.
Should not have
• Landscape photos

```html
<!DOCTYPE html>
<html lang="en">
<head>
<meta charset="UTF-8">
<title>Norvane Investment Management</title>
<link rel="stylesheet" href="https://fonts.googleapis.com/css2?family=Open+Sans:wght@400;600&family=Roboto:wght@400;500&display=swap">
<style>
  :root {
    --backdrop-dark: #3a3a3a;
    --backdrop-mid: #4a4744;
    --backdrop-warm: #5a4c40;
    --text-light: #ffffff;
    --button-top: #5a5a5a;
    --button-bottom: #2a2a2a;
    --active-top: #7cc4f2;
    --active-bottom: #4a97d2;
    --rule: #a9a9a9;
  }
  * { margin: 0; padding: 0; box-sizing: border-box; }
  html, body { width: 1200px; height: 612px; overflow: hidden; }
  body {
    position: relative;
    font-family: "Open Sans", sans-serif;
    color: var(--text-light);
    background: var(--backdrop-dark);
  }
  .hero-backdrop {
    position: absolute; inset: 0;
    background:
      radial-gradient(ellipse at 70% 70%, var(--backdrop-warm) 0%, transparent 60%),
      linear-gradient(180deg, var(--backdrop-mid) 0%, var(--backdrop-dark) 100%);
  }
  .brand {
    position: absolute; top: 38px; left: 0; width: 1200px;
    display: flex; justify-content: center; align-items: center; gap: 12px;
  }
  .brand-square { width: 44px; height: 44px; background: var(--text-light); }
  .brand-name {
    font-family: "Open Sans", sans-serif; font-weight: 600;
    font-size: 44px; letter-spacing: 1px; color: var(--text-light); line-height: 1;
  }
  .site-nav { position: absolute; left: 99px; top: 193px; }
  .nav-button {
    position: absolute; left: 0; width: 257px; height: 70px;
    display: flex; align-items: center; padding-left: 23px;
    font-family: "Roboto", sans-serif; font-size: 17.5px; line-height: 26px;
    color: var(--text-light); text-decoration: none;
    border: 1.5px solid var(--text-light); border-radius: 7px;
    background: linear-gradient(180deg, var(--button-top), var(--button-bottom));
  }
  .nav-button.is-active { border: none; background: none; }
  .nav-button .tab-shape { position: absolute; left: -1px; top: -1px; z-index: 0; }
  .nav-button span { position: relative; z-index: 1; }
  .nav-about { top: 0; }
  .nav-approach { top: 95px; }
  .nav-contact { top: 189px; }
  .about-copy { position: absolute; left: 414px; top: 193px; width: 684px; }
  .about-lead {
    font-size: 19px; line-height: 31px; font-weight: 600; text-align: justify;
  }
  .about-body {
    margin-top: 14px; font-size: 13px; line-height: 26px; font-weight: 600; text-align: justify;
  }
  .footer-rule {
    position: absolute; left: 99px; top: 537px; width: 1002px; height: 1.5px; background: var(--rule);
  }
  .site-footer {
    position: absolute; left: 99px; top: 566px; width: 1062px;
    display: flex; justify-content: space-between;
    font-family: "Roboto", sans-serif; font-weight: 500; font-size: 14px;
  }
  .footer-links { display: flex; gap: 0; }
  .footer-links a { color: var(--text-light); text-decoration: none; }
  .footer-links .divider { margin: 0 19px; }
  .footer-code { margin-left: 38px; }
</style>
</head>
<body>
  <div class="hero-backdrop" role="img" aria-label="Dimmed photo of stacked coins with a hand placing a coin beside a small red house model"></div>

  <header class="brand">
    <div class="brand-square"></div>
    <div class="brand-name">NORVANE</div>
  </header>

  <nav class="site-nav">
    <a class="nav-button nav-about is-active" href="#about">
      <svg class="tab-shape" width="290" height="72" viewBox="0 0 290 72">
        <defs>
          <linearGradient id="activeFill" x1="0" y1="0" x2="0" y2="1">
            <stop offset="0" stop-color="var(--active-top)"/>
            <stop offset="1" stop-color="var(--active-bottom)"/>
          </linearGradient>
        </defs>
        <path d="M8 1 H251 a7 7 0 0 1 7 7 V22 L285 36 L258 50 V64 a7 7 0 0 1 -7 7 H8 a7 7 0 0 1 -7 -7 V8 a7 7 0 0 1 7 -7 Z"
              fill="url(#activeFill)" stroke="#ffffff" stroke-width="1.5"/>
      </svg>
      <span>ABOUT NORVANE</span>
    </a>
    <a class="nav-button nav-approach" href="#approach"><span>OUR APPROACH<br>AND PHILOSOPHY</span></a>
    <a class="nav-button nav-contact" href="#contact"><span>CONTACT US</span></a>
  </nav>

  <main class="about-copy" id="about">
    <p class="about-lead">Norvane Investment Management was founded in 2016 with a clear vision to create an independent and nimble firm focused on generating superior risk-adjusted</p>
    <p class="about-body">Norvane has designed an innovative investment approach which aims to harness the best elements of alter native investment management whilst reducing its recognised shortcomings. We are a performance and client focused firm, committed to building lasting relationships, treating our clients like partners rather than revenue streams.</p>
  </main>

  <div class="footer-rule"></div>
  <footer class="site-footer">
    <div class="copyright">Copyrights @ 2017 Norvane. All Rights Reserved</div>
    <div class="footer-links">
      <a href="#disclaimer">Disclaimer</a><span class="divider">|</span>
      <a href="#terms">Terms and Conditions</a><span class="divider">|</span>
      <a href="#stewardship">Stewardship</a><span class="divider">|</span>
      <a href="#pillar">Pillar III</a>
      <span class="footer-code">C20</span>
    </div>
  </footer>
</body>
</html>
```